QAMBRO THERAPEUTICS

physical therapy company. need a flashy image and named logo, website link, that I can also use on Letterhead and business cards. Clean, sharp, modern, eye catching. 3 colors? Some shine. Needs to stand out and not be trendy or too much cursive . Androgynous image of a human body is ok. A spine included is ok. Prefer lines to curves for font types. Warm colors but strong impact. Will need to have some contact info and border mission statement on it.
Updates

Target Market(s)

Target market is large corporations, wealthy individuals, medical doctors

Industry/Entity Type

Medical, physical therapy

Contact Information for Business Card

Name, Owner, phone, email, and website

Colors
0054AA
0677BA
7BADD7
CADEEF
E8F1F8

Requirements
Must have
• See above- something about BALANCE, wellness, strength etc
Nice to have
• Contrast, depth
Should not have
• No cursive

```html
<!DOCTYPE html>
<html lang="en">
<head>
<meta charset="utf-8">
<title>Qambro Therapeutics — Business Card</title>
<link rel="stylesheet" href="https://fonts.googleapis.com/css2?family=Bebas+Neue&family=Roboto:wght@400&display=swap">
<style>
  :root {
    --page-bg: #262626;
    --card-blue: #0677BA;
    --card-blue-deep: #0054AA;
    --card-blue-light: #7BADD7;
    --ink-white: #FFFFFF;
    --rule: #7BADD7;
  }
  html, body {
    margin: 0;
    padding: 0;
    width: 1200px;
    height: 1108px;
    overflow: hidden;
    background: var(--page-bg);
  }
  .canvas {
    position: relative;
    width: 1200px;
    height: 1108px;
  }
  .card {
    position: absolute;
    top: 189px;
    width: 460px;
    height: 730px;
    border-radius: 26px;
    background: var(--card-blue);
    overflow: hidden;
    color: var(--ink-white);
  }
  .card--front { left: 110px; }
  .card--back  { left: 630px; }

  .brand {
    position: absolute;
    left: 48px;
    right: 40px;
    top: 78px;
    font-family: "Bebas Neue", "Oswald", sans-serif;
    font-weight: 400;
    color: var(--ink-white);
    line-height: 0.86;
    margin: 0;
    white-space: nowrap;
  }
  .brand__name { display: block; font-size: 142px; letter-spacing: 0; }
  .brand__tag  { display: block; font-size: 76px; letter-spacing: 0.5px; margin-top: 8px; }

  .person {
    position: absolute;
    left: 0;
    right: 0;
    top: 440px;
    text-align: center;
  }
  .person__name {
    font-family: "Bebas Neue", "Oswald", sans-serif;
    font-size: 46px;
    line-height: 1;
    letter-spacing: 0.5px;
    margin: 0;
  }
  .person__role {
    font-family: "Roboto", Arial, sans-serif;
    font-size: 23px;
    letter-spacing: 1px;
    margin: 2px 0 0;
  }

  .contact-icons {
    position: absolute;
    left: 50px;
    right: 50px;
    top: 540px;
    display: flex;
    align-items: center;
    gap: 10px;
  }
  .contact-icons__rule {
    flex: 1;
    height: 1px;
    background: var(--rule);
  }
  .contact-icons svg { display: block; }

  .contact-list {
    position: absolute;
    left: 0;
    right: 0;
    top: 600px;
    margin: 0;
    padding: 0;
    list-style: none;
    text-align: center;
    font-family: "Roboto", Arial, sans-serif;
    font-size: 23px;
    line-height: 1.38;
    letter-spacing: 0.8px;
  }

  .back-pattern {
    position: absolute;
    inset: 0;
    background: linear-gradient(135deg, #0A82C8 0%, var(--card-blue) 50%, #05609F 100%);
  }
  .back-mark {
    position: absolute;
    left: 0;
    right: 0;
    top: 420px;
    text-align: center;
    font-family: "Bebas Neue", "Oswald", sans-serif;
    color: var(--ink-white);
    line-height: 0.9;
    margin: 0;
  }
  .back-mark__name { display: block; font-size: 58px; }
  .back-mark__tag  { display: block; font-size: 26px; }
</style>
</head>
<body>
<main class="canvas">

  <section class="card card--front" aria-label="Business card front">
    <h1 class="brand">
      <span class="brand__name">QAMBRO</span>
      <span class="brand__tag">THERAPEUTICS</span>
    </h1>

    <div class="person">
      <p class="person__name">DANIEL HARPER</p>
      <p class="person__role">Managing Director</p>
    </div>

    <div class="contact-icons">
      <span class="contact-icons__rule"></span>
      <svg width="40" height="40" viewBox="0 0 40 40" aria-label="Phone">
        <rect width="40" height="40" rx="5" fill="#FFFFFF"/>
        <path d="M11 15 q9 -7 18 0 l-2 4 h-4 l-1-2 h-4 l-1 2 h-4 z" fill="#0677BA"/>
        <rect x="12" y="21" width="16" height="9" rx="2" fill="#0677BA"/>
        <circle cx="20" cy="25.5" r="2.2" fill="#FFFFFF"/>
      </svg>
      <svg width="40" height="40" viewBox="0 0 40 40" aria-label="Email">
        <rect width="40" height="40" rx="5" fill="#FFFFFF"/>
        <rect x="9" y="12" width="22" height="16" fill="none" stroke="#0677BA" stroke-width="2.5"/>
        <path d="M9 12 L20 22 L31 12 M9 28 L17 20 M31 28 L23 20" fill="none" stroke="#0677BA" stroke-width="2"/>
      </svg>
      <svg width="40" height="40" viewBox="0 0 40 40" aria-label="Website">
        <rect width="40" height="40" rx="5" fill="#FFFFFF"/>
        <circle cx="20" cy="20" r="11" fill="#0677BA"/>
        <ellipse cx="20" cy="20" rx="5" ry="11" fill="none" stroke="#FFFFFF" stroke-width="1.5"/>
        <path d="M9 20 H31 M11 14 H29 M11 26 H29" stroke="#FFFFFF" stroke-width="1.5"/>
      </svg>
      <span class="contact-icons__rule"></span>
    </div>

    <ul class="contact-list">
      <li>044-987 654 321</li>
      <li>info@qambrotherapy.com</li>
      <li>www.qambrotherapy.com</li>
    </ul>
  </section>

  <section class="card card--back" aria-label="Business card back">
    <div class="back-pattern" role="img" aria-label="Faint repeating tone-on-tone brand name pattern across the card"></div>
    <p class="back-mark">
      <span class="back-mark__name">QAMBRO</span>
      <span class="back-mark__tag">THERAPEUTICS</span>
    </p>
  </section>

</main>
</body>
</html>
```